Business Cards - Brightpath Horizon

need to design unique business card for my mortgage business. I need to design credit card style business card for my business or any unique idea that you might have

Target Market(s)

Home Loan customers

Industry/Entity Type

Mortgage Brokerage

Contact Information for Business Card

please design credit card style or very unique style business card

Colors

Designer to choose colors to be used in the design.

Requirements
Must have
• Name
• position
• Phone number
• fax number
• email address
• website address
• social media address
• All above fields will be provided once design in finalised

```html
<!DOCTYPE html>
<html lang="en">
<head>
<meta charset="utf-8">
<title>Brightpath Horizon – Business Card</title>
<link rel="stylesheet" href="https://fonts.googleapis.com/css2?family=Roboto:wght@400;700&family=Roboto+Condensed:wght@700&display=swap">
<style>
  :root {
    --backdrop: #2b2b2c;
    --brand-blue: #0f2fd6;
    --card-white: #f3f3f3;
    --text-grey: #4a4a4a;
    --accent-orange: #f7931e;
    --rule-grey: #6d6d6d;
    --wash-blue: rgba(120, 140, 220, 0.22);
    --wash-orange: rgba(247, 170, 90, 0.2);
  }
  * { margin: 0; padding: 0; box-sizing: border-box; }
  html, body {
    width: 1200px; height: 960px; overflow: hidden;
    background: var(--backdrop);
    font-family: "Roboto", Arial, sans-serif;
  }
  .canvas { position: relative; width: 1200px; height: 960px; }
  .card {
    position: absolute; left: 320px; width: 600px; height: 342px;
    border-radius: 22px; overflow: hidden;
  }
  .card-front { top: 108px; background: var(--brand-blue); }
  .card-back {
    top: 493px;
    background: linear-gradient(135deg, #f6f6f6 0%, var(--card-white) 60%, #ececec 100%);
  }
  .brand-name {
    position: absolute; left: 0; right: 0; top: 142px;
    text-align: center; color: #fff;
    font-weight: 700; font-size: 40px; letter-spacing: 1px;
  }
  .social-links {
    position: absolute; top: 279px; left: 237px;
    display: flex; gap: 4px;
  }
  .social-dot {
    width: 30px; height: 30px; border-radius: 50%; background: #fff;
    display: flex; align-items: center; justify-content: center;
  }
  .social-dot svg { width: 16px; height: 16px; }
  .backdrop-wash {
    position: absolute; pointer-events: none;
  }
  .backdrop-wash.roof-blue {
    left: 170px; top: 10px; width: 440px; height: 230px;
    background: radial-gradient(ellipse at 60% 55%, var(--wash-blue) 0%, rgba(120,140,220,0.12) 45%, rgba(120,140,220,0) 75%);
  }
  .backdrop-wash.roof-orange {
    left: -40px; top: 170px; width: 400px; height: 200px;
    background: radial-gradient(ellipse at 45% 60%, var(--wash-orange) 0%, rgba(247,170,90,0.1) 45%, rgba(247,170,90,0) 75%);
  }
  .contact-list {
    position: absolute; left: 25px; top: 24px;
    font-size: 14.5px; line-height: 19.3px; color: var(--text-grey);
  }
  .contact-list b { color: var(--brand-blue); font-weight: 700; }
  .address { margin-top: 3px; }
  .holder-mark {
    position: absolute; left: 0; width: 16px; height: 17px; background: var(--brand-blue);
  }
  .holder-mark.top { top: 253px; }
  .holder-mark.bottom { top: 277px; }
  .holder-name {
    position: absolute; left: 25px; top: 249px;
    font-family: "Roboto Condensed", "Arial Narrow", sans-serif; font-weight: 700;
    font-size: 21px; color: var(--brand-blue);
  }
  .holder-title {
    position: absolute; left: 25px; top: 276px;
    font-size: 14.5px; color: var(--accent-orange);
  }
  .base-rule {
    position: absolute; left: 28px; right: 30px; top: 298px;
    height: 1px; background: var(--rule-grey);
  }
  .back-brand {
    position: absolute; right: 32px; top: 278px;
    font-size: 14px; font-weight: 700; color: var(--brand-blue);
  }
</style>
</head>
<body>
<main class="canvas">
  <section class="card card-front">
    <div class="brand-name">Brightpath Horizon</div>
    <div class="social-links" aria-label="Social media">
      <span class="social-dot" aria-label="Website">
        <svg viewBox="0 0 16 16" fill="none" stroke="#0f2fd6" stroke-width="1.4"><circle cx="8" cy="8" r="6"/><path d="M2 8h12M8 2c2 2 2 10 0 12M8 2c-2 2-2 10 0 12"/></svg>
      </span>
      <span class="social-dot" aria-label="Email">
        <svg viewBox="0 0 16 16" fill="none" stroke="#0f2fd6" stroke-width="1.4"><rect x="2" y="4" width="12" height="8"/><path d="M2 4l6 5 6-5"/></svg>
      </span>
      <span class="social-dot" aria-label="Chat">
        <svg viewBox="0 0 16 16" fill="none" stroke="#0f2fd6" stroke-width="1.4"><path d="M2 3h12v8H7l-3 3v-3H2z"/></svg>
      </span>
      <span class="social-dot" aria-label="Profile">
        <svg viewBox="0 0 16 16" fill="none" stroke="#0f2fd6" stroke-width="1.4"><circle cx="8" cy="5.5" r="2.5"/><path d="M3 14c0-3 2.2-4.5 5-4.5s5 1.5 5 4.5"/></svg>
      </span>
    </div>
  </section>

  <section class="card card-back">
    <div class="backdrop-wash roof-blue" role="img" aria-label="Faint large house roof with window, in pale blue"></div>
    <div class="backdrop-wash roof-orange" role="img" aria-label="Faint house roof with window, in pale orange"></div>
    <div class="contact-list">
      <div><b>P:</b> 555 214 7390</div>
      <div><b>F:</b> 555 214 7391</div>
      <div><b>E:</b> hello@brightpath.com</div>
      <div><b>W:</b> www.brightpath.com</div>
      <div class="address">2140 Alder Crest Way<br>Cedar Falls, Oregon 97301</div>
    </div>
    <span class="holder-mark top"></span>
    <span class="holder-mark bottom"></span>
    <div class="holder-name">DANIEL REYES</div>
    <div class="holder-title">CEO/FOUNDER</div>
    <div class="back-brand">Brightpath Horizon</div>
    <div class="base-rule"></div>
  </section>
</main>
</body>
</html>
```